Modern Verdell Tree Care Website

I need a website for a full service Tree Care company. The company provides tree pruning, tree removal, tree preservation, emergency services, stump grinding, and emergency tree services.

Target Market(s)

Customers that need tree services

Industry/Entity Type

Landscaping, Tree Services

Coding

Coded - Design and coding required

Number of Pages Required

5+ page

Font styles to use
Sans Serif

Requirements
Must have
• Good clean design that showcases the services the company provides.
Nice to have
• Services page; contact form, blog, home page, about page

```html
<!DOCTYPE html>
<html lang="en">
<head>
<meta charset="utf-8">
<title>Verdell Tree Care – Services</title>
<link rel="stylesheet" href="https://fonts.googleapis.com/css2?family=Montserrat:wght@400;500;600;700;800&display=swap">
<style>
:root{
  --green:#6fb53a;
  --green-dark:#5a9e2b;
  --orange:#f7a93a;
  --ink:#2d3a40;
  --slate:#4a5a62;
  --text:#3a3a3a;
  --light:#f4f3f0;
  --star:#f5a623;
  --white:#fff;
}
*{margin:0;padding:0;box-sizing:border-box}
html,body{width:1200px;height:2264px;overflow:hidden}
body{font-family:"Montserrat",sans-serif;color:var(--text);background:var(--white);position:relative}
.abs{position:absolute}

/* header */
.site-header{position:absolute;left:0;top:0;width:1200px;height:81px;background:var(--white)}
.brand{position:absolute;display:flex;align-items:center;gap:10px;font-weight:800;color:var(--slate);text-transform:uppercase;letter-spacing:.5px;white-space:nowrap}
.brand-mark{background:var(--green);flex:none}
.site-header .brand{left:97px;top:24px;height:34px;font-size:15px;letter-spacing:.2px}
.site-header .brand-mark{width:34px;height:34px}
.main-nav{position:absolute;left:352px;top:34px;display:flex;gap:0}
.main-nav a{font-size:13px;font-weight:500;color:var(--ink);text-decoration:none;text-transform:uppercase;position:absolute;white-space:nowrap}
.main-nav a.active{color:var(--green)}
.main-nav a.active::after{content:"";position:absolute;left:15px;right:15px;top:22px;height:2px;background:var(--ink)}
.call-btn{position:absolute;left:945px;top:16px;width:175px;height:46px;border-radius:23px;background:var(--green);color:#fff;font-size:14px;display:flex;align-items:center;gap:8px;padding-left:19px}
.call-btn .ic{width:25px;height:25px;border-radius:50%;background:#fff;display:flex;align-items:center;justify-content:center}

/* hero */
.hero{position:absolute;left:0;top:81px;width:1200px;height:378px;overflow:hidden}
.hero-photo{position:absolute;inset:0;background:linear-gradient(120deg,#7d8c5a 0%,#a9b36a 35%,#c9d46b 55%,#6d8a3e 100%)}
.hero .eyebrow{position:absolute;left:118px;top:130px;font-size:17px;color:#fff;letter-spacing:.5px}
.hero h1{position:absolute;left:113px;top:155px;font-size:38px;font-weight:800;color:#fff}

/* services */
.section-icon{position:absolute;left:573px;top:523px;width:28px;height:28px;background:var(--green)}
.section-title{position:absolute;left:0;width:1200px;top:553px;text-align:center;font-size:35px;font-weight:800;color:var(--ink)}
.section-title span{color:var(--green);font-weight:500}
.title-rule{position:absolute;left:552px;top:601px;width:68px;height:3px;background:linear-gradient(90deg,var(--green) 55%,var(--orange) 55%)}
.intro{position:absolute;left:215px;top:633px;width:740px;text-align:center;font-size:15.5px;line-height:23px;color:var(--text)}
.card{position:absolute;width:300px;height:270px;background:var(--green);border-bottom-right-radius:38px;border-top-left-radius:22px;overflow:hidden}
.card .photo{position:absolute;left:0;top:0;width:300px;height:216px;border-bottom-right-radius:38px;border-top-left-radius:22px}
.card .label{position:absolute;left:0;right:0;top:216px;height:54px;display:flex;align-items:center;justify-content:center;color:#fff;font-weight:700;font-size:17.5px;text-transform:uppercase;letter-spacing:.2px}

/* testimonials */
.reviews{position:absolute;left:0;top:1416px;width:1200px;height:521px;background:var(--light);overflow:hidden}
.reviews-bg{position:absolute;inset:0;background:linear-gradient(160deg,#fbb24a,#f8a233)}
.reviews h2{position:absolute;left:127px;top:144px;font-size:28px;line-height:36px;font-weight:800;color:#fff;text-transform:uppercase}
.reviews .rule{position:absolute;left:127px;top:259px;width:58px;height:3px;background:#fff}
.reviews .tag{position:absolute;left:128px;top:286px;font-size:17px;font-weight:700;color:#fff}
.reviews .big-stars{position:absolute;left:128px;top:310px;font-size:24px;color:#fff;letter-spacing:1px}
.reviews .meta{position:absolute;left:127px;top:344px;font-size:14px;color:#fff}
.bubble{position:absolute;width:330px;height:330px;border-radius:50%;background:#fff;box-shadow:0 0 12px rgba(0,0,0,.08);display:flex;align-items:center;justify-content:center}
.bubble .ring{position:absolute;inset:10px;border-radius:50%;border:2px solid var(--green)}
.bubble .ring.tan{border-color:#e8c9a0}
.bubble .content{position:relative;width:245px;text-align:center}
.bubble .quote-mark{font-size:72px;line-height:48px;height:38px;font-weight:800;color:var(--orange);font-family:Georgia,serif}
.bubble p{font-size:13px;line-height:23px;color:var(--text);margin-top:4px}
.bubble .name{font-size:15px;font-weight:600;color:var(--ink);margin-top:8px}
.bubble .stars{font-size:18px;color:var(--star);letter-spacing:1px}
.arrow{position:absolute;top:235px;width:20px;height:30px}

/* footer */
.site-footer .brand{left:0;width:1200px;top:1988px;justify-content:center;font-size:30px}
.site-footer .brand-mark{width:54px;height:54px}
.f-rule{position:absolute;left:113px;width:995px;height:1px;background:#cfcfcf}
.foot-nav{position:absolute;left:0;width:1200px;top:2080px;display:flex;justify-content:center;align-items:center;gap:0}
.foot-nav a{font-size:15px;font-weight:700;color:var(--ink);text-decoration:none;text-transform:uppercase}
.foot-nav i{display:block;width:4px;height:4px;background:var(--green);margin:0 38px}
.contact{position:absolute;top:2151px;display:flex;align-items:center;gap:6px;font-size:14px;font-weight:600;color:var(--ink)}
.contact .ic{width:36px;height:36px;border-radius:50%;background:var(--green);display:flex;align-items:center;justify-content:center}
.social{position:absolute;top:2155px;width:26px;height:26px;border-radius:50%}
.copyright{position:absolute;left:0;top:2214px;width:1200px;height:50px;background:var(--light);text-align:center;line-height:50px;font-size:13.5px;color:var(--ink)}
</style>
</head>
<body>

<header class="site-header">
  <div class="brand"><span class="brand-mark"></span>Verdell Tree Care</div>
  <nav class="main-nav">
    <a style="left:0">Home</a>
    <a style="left:84px">About Us</a>
    <a class="active" style="left:197px">Services</a>
    <a style="left:306px">Blog</a>
    <a style="left:387px">Review</a>
    <a style="left:483px">Contact Us</a>
  </nav>
  <div class="call-btn"><span class="ic"><svg width="14" height="14" viewBox="0 0 24 24"><path fill="#6fb53a" d="M6.6 10.8a15.1 15.1 0 0 0 6.6 6.6l2.2-2.2c.3-.3.7-.4 1-.2 1.1.4 2.3.6 3.6.6.6 0 1 .4 1 1V20c0 .6-.4 1-1 1A17 17 0 0 1 3 4c0-.6.4-1 1-1h3.5c.6 0 1 .4 1 1 0 1.3.2 2.5.6 3.6.1.3 0 .7-.2 1z"/></svg></span>(555) 214 3086</div>
</header>

<section class="hero">
  <div class="hero-photo" role="img" aria-label="Arborists in hi-vis shirts cutting fallen branches with a pole saw on a lawn"></div>
  <svg class="abs" style="left:0;top:0" width="1200" height="378"><polygon points="0,0 592,0 385,378 0,378" fill="#6cb53b"/></svg>
  <p class="eyebrow">WHAT WE DO</p>
  <h1>OUR SERVICES</h1>
</section>

<section class="services">
  <span class="section-icon"></span>
  <h2 class="section-title">SERVICES <span>PROVIDE</span></h2>
  <span class="title-rule"></span>
  <p class="intro">At Verdell Tree Care, we are more than just a tree service company, we are stewards of our beautiful trees. With a passion deeply rooted in arboriculture, we embark on a mission to promote the health, beauty, and safety of your trees and landscapes.</p>

  <article class="card" style="left:120px;top:751px"><div class="photo" role="img" aria-label="Pruning shears cutting a tree branch" style="background:linear-gradient(135deg,#8aa35a,#5f7d3a)"></div><div class="label">Tree Pruning</div></article>
  <article class="card" style="left:450px;top:748px"><div class="photo" role="img" aria-label="Chainsaw cutting into a tree trunk" style="background:linear-gradient(135deg,#4f6b2e,#6e5034)"></div><div class="label">Tree Removal</div></article>
  <article class="card" style="left:777px;top:751px"><div class="photo" role="img" aria-label="Shovel planting a young tree in soil" style="background:linear-gradient(135deg,#6f9a3c,#6b4a32)"></div><div class="label">Tree Preservation</div></article>
  <article class="card" style="left:118px;top:1055px"><div class="photo" role="img" aria-label="Tree stump being ground down by a machine" style="background:linear-gradient(135deg,#4d6636,#8a6040)"></div><div class="label">Stump Grinding</div></article>
  <article class="card" style="left:449px;top:1052px"><div class="photo" role="img" aria-label="Large leafy tree canopy against blue sky" style="background:linear-gradient(135deg,#4d7fa8,#2f4a24 45%)"></div><div class="label">Tree Emergency Services</div></article>
  <article class="card" style="left:776px;top:1055px"><div class="photo" role="img" aria-label="Climber in harness with chainsaw working in a tree" style="background:linear-gradient(135deg,#3e5a2a,#7b8d3a)"></div><div class="label">Cabling &amp; Bracing</div></article>
</section>

<section class="reviews">
  <div class="reviews-bg" role="img" aria-label="Faded image of an arborist climbing a tree with a chainsaw"></div>
  <svg class="abs" style="left:0;top:0" width="1200" height="521"><polygon points="556,0 1200,0 1200,521 330,521" fill="#f4f3f0"/></svg>
  <h2>What people<br>are saying<br>about us</h2>
  <span class="rule"></span>
  <p class="tag">EXLLENT SERVICE</p>
  <p class="big-stars">★★★★★</p>
  <p class="meta">4.8 Rating &nbsp;|&nbsp; 3500 Reviews</p>

  <svg class="arrow" style="left:372px" viewBox="0 0 20 30"><path d="M15 4 5 15l10 11" fill="none" stroke="#6fb53a" stroke-width="3"/></svg>
  <div class="bubble" style="left:400px;top:85px"><span class="ring"></span><div class="content"><div class="quote-mark">&ldquo;</div><p>“Lorem ipsum dolor sit amet, consectetur adipiscing elit, sed do eiusmod tempor incididunt ut labore et dolore magna aliqua Quis ipsum suspendisse ultrices gravida Risus commodo viverra maecenas ”</p><div class="name">Dana Whitlow</div><div class="stars">★★★★★</div></div></div>
  <div class="bubble" style="left:745px;top:83px"><span class="ring"></span><div class="content"><div class="quote-mark">&ldquo;</div><p>“Lorem ipsum dolor sit amet, consectetur adipiscing elit, sed do eiusmod tempor incididunt ut labore et dolore magna aliqua Quis ipsum suspendisse ultrices gravida Risus commodo viverra maecenas ”</p><div class="name">Dana Whitlow</div><div class="stars">★★★★★</div></div></div>
  <div class="bubble" style="left:1108px;top:85px"><span class="ring tan"></span><div class="content"><div class="quote-mark">&ldquo;</div><p>“Lorem ipsum dolor sit amet, consectetur adipiscing elit, sed do eiusmod tempor incididunt ut labore et dolore magna aliqua Quis ipsum suspendisse ultrices gravida Risus commodo viverra maecenas ”</p><div class="name">Dana Whitlow</div><div class="stars">★★★★★</div></div></div>
  <svg class="arrow" style="left:1086px" viewBox="0 0 20 30"><path d="M5 4l10 11L5 26" fill="none" stroke="#6fb53a" stroke-width="3"/></svg>
</section>

<footer class="site-footer">
  <div class="brand"><span class="brand-mark"></span>Verdell Tree Care</div>
  <span class="f-rule" style="top:2054px"></span>
  <nav class="foot-nav">
    <a>Home</a><i></i><a>About Us</a><i></i><a>Services</a><i></i><a>Blogs</a><i></i><a>Reviews</a><i></i><a>Contact</a>
  </nav>
  <span class="f-rule" style="top:2124px"></span>
  <div class="contact" style="left:206px"><span class="ic"><svg width="18" height="18" viewBox="0 0 24 24"><path fill="#fff" d="M6.6 10.8a15.1 15.1 0 0 0 6.6 6.6l2.2-2.2c.3-.3.7-.4 1-.2 1.1.4 2.3.6 3.6.6.6 0 1 .4 1 1V20c0 .6-.4 1-1 1A17 17 0 0 1 3 4c0-.6.4-1 1-1h3.5c.6 0 1 .4 1 1 0 1.3.2 2.5.6 3.6.1.3 0 .7-.2 1z"/></svg></span>(555) 214-3086</div>
  <div class="contact" style="left:441px"><span class="ic"><svg width="18" height="18" viewBox="0 0 24 24"><path fill="#fff" d="M6.6 10.8a15.1 15.1 0 0 0 6.6 6.6l2.2-2.2c.3-.3.7-.4 1-.2 1.1.4 2.3.6 3.6.6.6 0 1 .4 1 1V20c0 .6-.4 1-1 1A17 17 0 0 1 3 4c0-.6.4-1 1-1h3.5c.6 0 1 .4 1 1 0 1.3.2 2.5.6 3.6.1.3 0 .7-.2 1z"/></svg></span>(555) 407-6621</div>
  <div class="contact" style="left:643px"><span class="ic"><svg width="18" height="14" viewBox="0 0 18 14"><rect x="1" y="1" width="16" height="12" rx="1.5" fill="#fff"/><path d="M1.5 2 9 8l7.5-6" fill="none" stroke="#6fb53a" stroke-width="1.5"/></svg></span>&nbsp;hello@verdelltreecare.com</div>
  <span class="social" style="left:937px;background:var(--ink)"></span>
  <span class="social" style="left:975px;background:var(--green)"></span>
  <span class="social" style="left:1014px;background:var(--green)"></span>
  <span class="social" style="left:1053px;background:var(--green)"></span>
  <div class="copyright">Copyright © 2024 Verdell Tree Care | &nbsp;All Right Reserved</div>
</footer>

</body>
</html>
```